New web page, 2 companies on the one page

A new web page for an engineering consultancy and maintenance management company

Corlett & Associates is the parent company covering the design and consultancy
Valtrix Engineering is the Maintenance and Reliability company

Target Market(s)

Food & Beverage, ingredients Manufacturing
engineering managers

Coding

Coded - Design and coding required

Number of Pages Required

1 page

Font styles to use
Other font styles liked:
• Roboto

Colors
1861ab
85acd3
d0dfed
cee9f5

```html
<!DOCTYPE html>
<html lang="en">
<head>
<meta charset="utf-8">
<title>Corlett &amp; Associates</title>
<link href="https://fonts.googleapis.com/css2?family=Audiowide&family=Roboto:wght@400;500&display=swap" rel="stylesheet">
<style>
:root{
  --brand:#1e90d6;
  --brand-dark:#1861ab;
  --ink:#2b2b2b;
  --muted:#555;
  --sky:#85acd3;
  --pale:#d0dfed;
  --mist:#cee9f5;
  --footer:#1c1a1b;
  --white:#fff;
}
*{margin:0;padding:0;box-sizing:border-box}
html,body{width:1200px;height:3610px;overflow:hidden;background:var(--white)}
body{position:relative;font-family:Roboto,sans-serif;color:var(--ink)}
.display{font-family:Audiowide,sans-serif;font-weight:400}
.abs{position:absolute}
.center{left:0;width:1200px;text-align:center}

/* header */
.brand-mark{left:112px;top:44px;display:flex;align-items:center;gap:14px}
.brand-mark .dot{width:44px;height:44px;background:var(--brand)}
.brand-mark .name{font-family:Audiowide,sans-serif;font-size:22px;color:#333;line-height:1}
.nav{top:62px;right:110px;display:flex;gap:46px;font-family:Audiowide,sans-serif;font-size:14px}
.nav a{color:#222;text-decoration:none}
.nav a.active{color:var(--brand)}

/* hero */
.hero{top:135px;left:0;width:1200px;height:785px}
.hero-photo{position:absolute;inset:0;clip-path:polygon(0 0,100% 0,100% 678px,598px 742px,0 678px);
  background:linear-gradient(180deg,#2d86d0 0%,#7fbde6 38%,#cfe6f3 55%,#8a8a7a 66%,#b0703e 76%,#1d6fa6 88%,#0f5c93 100%)}
.hero-band{position:absolute;inset:0;background:var(--brand);clip-path:polygon(0 678px,598px 742px,1200px 678px,1200px 700px,598px 785px,0 700px)}
.hero-title{top:300px;font-size:40px;color:#2a2a2a}
.hero-sub{top:370px;font-size:21px;color:#1a1a1a}
.btn{display:flex;align-items:center;justify-content:center;background:var(--brand);color:var(--white);font-family:Audiowide,sans-serif;border-radius:2px}
.hero-btn{left:513px;top:421px;width:173px;height:59px;font-size:18px}

/* about */
.about-kicker{top:982px;font-size:32px;color:#2a2a2a}
.about-kicker .bars{display:inline-block;width:20px;height:18px;margin:0 12px;vertical-align:middle;
  background:linear-gradient(var(--ink) 0 4px,transparent 4px 7px,var(--brand) 7px 11px,transparent 11px 14px,var(--ink) 14px 18px)}
.about-title{top:1025px;font-size:36px;color:var(--brand)}
.about-copy{top:1105px;left:250px;width:700px;text-align:center;font-size:14.5px;line-height:25px;color:#444}
.about-copy p{margin-bottom:27px}
.about-btn{left:513px;top:1339px;width:174px;height:56px;font-size:16px}
.divider{top:1430px;left:0}

/* services */
.section-title{font-size:36px;color:#222}
.section-title span{color:var(--brand)}
.rule{width:44px;height:3px;background:var(--brand);left:578px}
.svc{width:236px}
.svc .img{height:197px}
.svc .label{margin-top:22px;text-align:center;font-family:Audiowide,sans-serif;font-size:15px;line-height:23px;color:#333}

/* feature */
.feature{top:2270px;left:0;width:1200px;height:528px;background:linear-gradient(180deg,#1e92da,#1b8cd2)}
.feature-edge{top:2270px;left:0}
.feature-art{left:168px;top:2368px;width:363px;height:380px;
  background:linear-gradient(180deg,#7fc0ea 0%,#4aa7e0 45%,#2a6f8a 75%,#1a5f8f 100%);
  clip-path:polygon(0 70px,50% 0,100% 70px,100% 330px,50% 380px,0 330px)}
.feature-kicker{left:608px;top:2410px;font-size:21px;color:var(--white)}
.feature-title{left:608px;top:2448px;font-size:30px;color:var(--white)}
.feature-copy{left:610px;top:2512px;width:488px;font-size:14px;line-height:26px;color:#eef7fd;text-align:justify}
.feature-btn{left:614px;top:2640px;width:166px;height:57px;border:2px solid var(--white);border-radius:3px;color:var(--white);
  font-family:Audiowide,sans-serif;font-size:18px;display:flex;align-items:center;justify-content:center}

/* newsletter */
.news-copy{top:2935px;left:220px;width:760px;text-align:center;font-size:14px;line-height:26px;color:#555}
.news-input{left:200px;top:3013px;width:800px;height:53px;border:1px solid #ccc;border-radius:3px;padding-left:24px;
  display:flex;align-items:center;font-size:13px;color:#444}
.news-btn{left:519px;top:3087px;width:163px;height:53px;font-size:16px}

/* footer */
.footer-shape{top:3185px;left:0}
.footer-brand{left:135px;top:3378px;display:flex;align-items:center;gap:12px}
.footer-brand .dot{width:40px;height:40px;background:var(--brand)}
.footer-brand .name{font-family:Audiowide,sans-serif;font-size:20px;color:var(--white)}
.f-head{font-size:18px;font-weight:400;color:var(--white);letter-spacing:.5px}
.f-list{list-style:none;font-size:14px;color:var(--white)}
.f-links li{height:32px;display:flex;align-items:center;gap:18px}
.f-links li::before{content:"»";font-size:14px}
.f-contact li{height:29px}
.f-news-copy{font-size:12.5px;line-height:28px;color:var(--white);width:230px}
.f-input{left:863px;top:3418px;width:225px;height:42px;background:var(--white);border-radius:3px;font-size:11px;color:#444;display:flex;align-items:center;padding-left:14px}
.f-btn{left:862px;top:3472px;width:99px;height:35px;font-size:12px;font-family:Roboto,sans-serif;font-weight:500}
.copyright{top:3573px;font-size:13px;color:#ddd}
</style>
</head>
<body>

<header>
  <div class="abs brand-mark"><span class="dot"></span><span class="name">CORLETT &amp; ASSOCIATES</span></div>
  <nav class="abs nav">
    <a class="active" href="#">HOME</a><a href="#">ABOUT US</a><a href="#">SERVICES</a><a href="#">NEWS</a><a href="#">CONTACT US</a>
  </nav>
</header>

<section class="abs hero">
  <div class="hero-photo" role="img" aria-label="Harbour city skyline with opera house and a boat on the water under a blue sky"></div>
  <div class="hero-band"></div>
</section>
<h1 class="abs center display hero-title">CORLETT &amp; ASSOCIATES</h1>
<p class="abs center display hero-sub">SED UT PERSPICIATIS UNDE OMNIS ISTE NATUS ERROR SIT</p>
<a class="abs btn hero-btn">READ MORE</a>

<section class="about">
  <h2 class="abs center display about-kicker"><span class="bars"></span>ABOUT US<span class="bars"></span></h2>
  <h3 class="abs center display about-title">CORLETT &amp; ASSOCIATES</h3>
  <div class="abs about-copy">
    <p>Corlett &amp; Associates is specialised manufacturing engineering support organisation that can provide fast, nimble, and flexible services.</p>
    <p>We have a proven track record in delivering tangible outcomes in process design and fit-out, project management, manufacturing process and maintenance design and execution.</p>
    <p>Our specialist focus in food manufacturing across a range of sectors allows our team to deliver real benefits to performance and recognition of the clients investment</p>
  </div>
  <a class="abs btn about-btn">READ MORE</a>
</section>

<svg class="abs divider" width="1200" height="56" viewBox="0 0 1200 56">
  <polygon points="0,2 598,42 1200,2 1200,6 598,54 0,6" fill="#1e90d6"/>
</svg>

<section class="services">
  <h2 class="abs center display section-title" style="top:1530px">OUR <span>SERVICES</span></h2>
  <div class="abs rule" style="top:1590px"></div>

  <div class="abs svc" style="left:112px;top:1634px"><div class="img" role="img" aria-label="Engineers reviewing a process control screen" style="background:linear-gradient(135deg,#3a5068,#8aa3b8)"></div><div class="label">PROCESS &amp;<br>FACILITIES DESIGN</div></div>
  <div class="abs svc" style="left:359px;top:1634px"><div class="img" role="img" aria-label="Team studying plans on a table with hard hats" style="background:linear-gradient(135deg,#c9d6e4,#6f93b8)"></div><div class="label">PROJECT<br>MANAGEMENT</div></div>
  <div class="abs svc" style="left:606px;top:1634px"><div class="img" role="img" aria-label="Technician working on industrial machinery" style="background:linear-gradient(135deg,#5a4a3c,#c27a3a)"></div><div class="label">ENGINEERING &amp;<br>MAINTENANCE</div></div>
  <div class="abs svc" style="left:853px;top:1634px"><div class="img" role="img" aria-label="Two colleagues planning at a wall board" style="background:linear-gradient(135deg,#4a3a34,#c9a08a)"></div><div class="label">MAINTENANCE<br>EXECUTION</div></div>

  <div class="abs svc" style="left:112px;top:1945px"><div class="img" role="img" aria-label="Automated vehicle assembly line" style="background:linear-gradient(135deg,#9fb3c6,#6b7f93)"></div><div class="label">MANUFACTURING<br>PERFORMANCE</div></div>
  <div class="abs svc" style="left:359px;top:1945px"><div class="img" role="img" aria-label="Engineer with a laptop at a control cabinet" style="background:linear-gradient(135deg,#b8a38a,#5a4a3a)"></div><div class="label">SCADA</div></div>
  <div class="abs svc" style="left:606px;top:1945px"><div class="img" role="img" aria-label="Camera inspecting a circuit board" style="background:linear-gradient(135deg,#dfe8f2,#5a7fb0)"></div><div class="label">VISION INSPECTION<br>SYSTEMS</div></div>
  <div class="abs svc" style="left:853px;top:1945px"><div class="img" role="img" aria-label="Hand touching a digital due diligence interface" style="background:linear-gradient(135deg,#0d2a4a,#3f86c4)"></div><div class="label">ACQUISITION<br>DUE DILIGENCE</div></div>
</section>

<section class="feature abs"></section>
<svg class="abs feature-edge" width="1200" height="56" viewBox="0 0 1200 56">
  <polygon points="0,0 1200,0 598,48" fill="#fff"/>
  <polygon points="0,0 598,48 1200,0 1200,6 598,56 0,6" fill="#6d6d6d"/>
</svg>
<div class="abs feature-art" role="img" aria-label="City skyline photograph framed in a shield shape"></div>
<h3 class="abs display feature-kicker">SED UT PERSPICIATIS UNDE</h3>
<h2 class="abs display feature-title">OMNIS ISTE NATUS ERROR SIT</h2>
<p class="abs feature-copy">Nemo enim ipsam voluptatem quia voluptas sit aspernatur aut odit aut fugit, sed quia consequuntur magni dolores eos qui ratione voluptatem sequi nesciunt.Neque porro quisquam est, qui dolorem ipsum quia dolor sit amet, consectetur, adipisci velit, sed quia non numquam eius</p>
<a class="abs feature-btn">READ MORE</a>

<section class="newsletter">
  <h2 class="abs center display section-title" style="top:2855px">OUR <span>NEWSLETTER</span></h2>
  <div class="abs rule" style="top:2912px"></div>
  <p class="abs news-copy">Sed ut perspiciatis unde omnis iste natus error sit voluptatem accusantium doloremque laudantium, totam rem aperiam, quae ab illo inventore veritatis et quasi architecto beatae vitae dicta sunt explicabo.</p>
  <div class="abs news-input">Enter Your Email :</div>
  <a class="abs btn news-btn">SUBMIT</a>
</section>

<svg class="abs footer-shape" width="1200" height="425" viewBox="0 0 1200 425">
  <polygon points="0,52 598,10 1200,52 1200,425 0,425" fill="#1e90d6"/>
  <polygon points="0,58 598,22 1200,58 1200,425 0,425" fill="#1c1a1b"/>
</svg>

<footer>
  <div class="abs footer-brand"><span class="dot"></span><span class="name">VALTRIX ENGINEERING</span></div>

  <h4 class="abs f-head" style="left:444px;top:3290px">LINKS</h4>
  <ul class="abs f-list f-links" style="left:446px;top:3328px">
    <li>HOME</li><li>ABOUT US</li><li>SERVICES</li><li>NEWS</li><li>CONTACT US</li>
  </ul>

  <h4 class="abs f-head" style="left:618px;top:3290px">CONTACT US</h4>
  <ul class="abs f-list f-contact" style="left:620px;top:3335px">
    <li>Tele : 000-555-0142</li><li>Fax : 000-555-0187</li><li>info@corlettassociates.com</li><li>61 NE 9th Dolor Sitam</li><li>Dummy Text 48120</li>
  </ul>

  <h4 class="abs f-head" style="left:863px;top:3290px">NEWSLETTER</h4>
  <p class="abs f-news-copy" style="left:863px;top:3338px">Sed ut perspiciatis unde error sit vol uptatem accusantium...</p>
  <div class="abs f-input">Enter Email Id :</div>
  <a class="abs btn f-btn">SUBMIT</a>

  <p class="abs center copyright">© Copyright 2021 Corlett &amp; Associates.All Rights Reserved</p>
</footer>

</body>
</html>
```